Coastline Premier Retreats Business Card Design

Design a business card for Coastline Premier Retreats. Look at the website for colors and reference. Card should have logo, name, title, office number, mobile number, email, URL and a tagline like, "Luxury Hotel & Resort Email Marketing" (This might change).

https://www.coastlinepremierretreats.example

The rest I will leave up to your imagination.

Contact Information for Business Card

Logo, name, title, office number, mobile number, email, URL and a tagline like, "Luxury Hotel & Resort Email Marketing" (This might change).

```html
<!DOCTYPE html>
<html lang="en">
<head>
<meta charset="utf-8">
<title>Coastline Premier Retreats – Business Card</title>
<link href="https://fonts.googleapis.com/css2?family=Montserrat:wght@400;500;700&display=swap" rel="stylesheet">
<style>
  :root {
    --ink: #1b1b1b;
    --paper: #ffffff;
    --accent: #f07a12;
    --text: #3a3a3a;
    --backdrop: #d9d9d9;
  }
  * { box-sizing: border-box; margin: 0; padding: 0; }
  html, body { width: 1200px; height: 901px; overflow: hidden; }
  body {
    background: var(--backdrop);
    font-family: "Montserrat", Arial, sans-serif;
    position: relative;
  }
  .card {
    position: absolute;
    width: 540px;
    height: 309px;
    border-radius: 22px;
    overflow: hidden;
    box-shadow: 0 10px 26px rgba(0,0,0,.25);
  }
  .card--front {
    left: 45px; top: 296px;
    background: var(--ink);
    display: flex; flex-direction: column; align-items: center; justify-content: center;
  }
  .brand-name {
    color: var(--paper);
    font-weight: 700;
    font-size: 30px;
    letter-spacing: 2px;
    text-transform: uppercase;
    text-align: center;
    line-height: 1.2;
  }
  .tagline {
    margin-top: 44px;
    color: var(--accent);
    font-size: 17px;
    font-weight: 500;
    letter-spacing: .5px;
  }
  .card--back {
    left: 615px; top: 296px;
    background: var(--paper);
    display: flex;
  }
  .brand-band {
    width: 150px;
    background: var(--ink);
    position: relative;
  }
  .brand-band .brand-name {
    position: absolute;
    left: 50%; top: 50%;
    width: 280px;
    font-size: 19px;
    transform: translate(-50%, -50%) rotate(-90deg);
  }
  .details { padding: 40px 0 0 38px; color: var(--text); }
  .person-name {
    color: var(--accent);
    font-weight: 700;
    font-size: 25px;
    letter-spacing: 1px;
  }
  .person-title { font-size: 13px; margin-top: 2px; }
  .address { font-size: 12.5px; line-height: 1.45; margin-top: 22px; }
  .contact-list { list-style: none; margin-top: 18px; font-size: 12.5px; }
  .contact-list li { display: flex; align-items: center; gap: 9px; margin-bottom: 6px; }
  .contact-list svg { width: 13px; height: 13px; fill: var(--accent); flex: none; }
</style>
</head>
<body>
  <section class="card card--front">
    <p class="brand-name">Coastline<br>Premier Retreats</p>
    <p class="tagline">Luxury Hotel &amp; Resort Email Marketing</p>
  </section>

  <section class="card card--back">
    <div class="brand-band">
      <p class="brand-name">Coastline Premier Retreats</p>
    </div>
    <div class="details">
      <h1 class="person-name">MARCUS HALE</h1>
      <p class="person-title">CEO/Founder</p>
      <p class="address">Po Box, 456 B Shore Rd<br>Bayview, CA 93012</p>
      <ul class="contact-list">
        <li><svg viewBox="0 0 16 16"><path d="M4 0h8a1 1 0 0 1 1 1v14a1 1 0 0 1-1 1H4a1 1 0 0 1-1-1V1a1 1 0 0 1 1-1zm1 2v10h6V2zm3 11a1 1 0 1 0 0 2 1 1 0 0 0 0-2z"/></svg>555.014.2200</li>
        <li><svg viewBox="0 0 16 16"><path d="M1 6c0-2 3-3 7-3s7 1 7 3v1h-3V5.5H4V7H1zm3 2h8l2 6H2zm4 1.5a2 2 0 1 0 0 4 2 2 0 0 0 0-4z"/></svg>+34 600 000 412</li>
        <li><svg viewBox="0 0 16 16"><path d="M0 3h16v10H0zm1.5 1.5L8 9l6.5-4.5V4h-13z"/></svg>info@coastlinepremierretreats.example</li>
        <li><svg viewBox="0 0 16 16"><path d="M8 0a8 8 0 1 0 0 16A8 8 0 0 0 8 0zm0 1.5c.8 0 1.8 1.8 2.1 5H5.9C6.2 3.3 7.2 1.5 8 1.5zM1.6 7.5h2.8c0 2 .4 3.7.9 5A6.5 6.5 0 0 1 1.6 7.5zm4.3 1h4.2c-.3 3.2-1.3 5-2.1 5s-1.8-1.8-2.1-5zm5.7 0h2.8a6.5 6.5 0 0 1-3.7 5c.5-1.3.9-3 .9-5z"/></svg>www.coastlinepremierretreats.example</li>
      </ul>
    </div>
  </section>
</body>
</html>
```